Business Card Design

We need a business card designed for our new company. Prefer a black card with white logo & writing.

Contact Information for Business Card

Ted Galloway, address: 7-4812 Fernhollow Road, Abbotsford, BC, V3K 8R2, Office Phone: 604-712-3390, Cell: 604-947-2164, Email: ted@resinworkshub.ca

Colors

Designer to choose only greyscale colors for use in the design.

```html
<!DOCTYPE html>
<html lang="en">
<head>
<meta charset="utf-8">
<title>Resin Works Hub – Business Card</title>
<link rel="stylesheet" href="https://fonts.googleapis.com/css2?family=Poppins:wght@300;400;700&display=swap">
<style>
  :root {
    --backdrop: #2a2a2c;
    --card: #1e1f22;
    --ink: #ffffff;
    --ink-soft: #e6e6e6;
    --rule: #9a9a9a;
  }
  * { box-sizing: border-box; margin: 0; padding: 0; }
  html, body {
    width: 1200px; height: 711px; overflow: hidden;
    background: var(--backdrop);
    font-family: "Poppins", sans-serif;
    color: var(--ink);
  }
  .canvas {
    position: relative; width: 1200px; height: 711px;
    display: flex; align-items: center; justify-content: center; gap: 40px;
  }
  .card {
    position: relative; width: 540px; height: 309px;
    background: var(--card); overflow: hidden;
  }
  .edge-band {
    position: absolute; width: 14px; background: var(--ink);
  }
  .edge-band--left { left: 0; bottom: 0; height: 170px; }
  .edge-band--right { right: 0; top: 0; height: 170px; }

  .brand {
    display: flex; align-items: center; gap: 10px;
    font-weight: 700; color: var(--ink); letter-spacing: 0.5px;
  }
  .brand__mark { width: 14px; height: 14px; background: var(--ink); flex: none; }

  .card--front { display: flex; align-items: center; justify-content: center; }
  .card--front .brand { font-size: 34px; }

  .card--back .brand {
    position: absolute; left: 38px; top: 108px; font-size: 22px;
  }
  .divider {
    position: absolute; left: 262px; top: 62px; width: 1px; height: 150px;
    background: var(--rule);
  }
  .contact {
    position: absolute; left: 290px; top: 56px;
  }
  .contact__name { font-size: 25px; font-weight: 300; line-height: 1.1; }
  .contact__name strong { font-weight: 700; }
  .contact__role { font-size: 11px; font-weight: 300; color: var(--ink-soft); margin-top: 2px; }
  .contact__list { list-style: none; margin-top: 16px; }
  .contact__item {
    display: flex; align-items: center; gap: 9px;
    font-size: 11px; font-weight: 300; line-height: 20px; color: var(--ink-soft);
  }
  .contact__item svg { width: 12px; height: 12px; flex: none; }
  .address {
    position: absolute; left: 0; right: 0; bottom: 26px;
    text-align: center; font-size: 12px; font-weight: 400; color: var(--ink-soft);
  }
</style>
</head>
<body>
<main class="canvas">
  <section class="card card--front" aria-label="Card front">
    <span class="edge-band edge-band--left"></span>
    <span class="edge-band edge-band--right"></span>
    <div class="brand"><span class="brand__mark"></span>Resin Works Hub</div>
  </section>

  <section class="card card--back" aria-label="Card back">
    <span class="edge-band edge-band--left"></span>
    <span class="edge-band edge-band--right"></span>
    <div class="brand"><span class="brand__mark"></span>Resin Works Hub</div>
    <span class="divider"></span>
    <div class="contact">
      <p class="contact__name"><strong>Ted</strong> Galloway</p>
      <p class="contact__role">Founder &amp; CEO</p>
      <ul class="contact__list">
        <li class="contact__item">
          <svg viewBox="0 0 24 24" fill="none" stroke="#fff" stroke-width="2"><path d="M5 3h4l2 5-2.5 1.5a11 11 0 0 0 6 6L16 13l5 2v4a2 2 0 0 1-2 2A16 16 0 0 1 3 5a2 2 0 0 1 2-2z"/></svg>
          604-712-3390
        </li>
        <li class="contact__item">
          <svg viewBox="0 0 24 24" fill="none" stroke="#fff" stroke-width="2"><rect x="6" y="2" width="12" height="20" rx="2"/><line x1="11" y1="18" x2="13" y2="18"/></svg>
          604-947-2164
        </li>
        <li class="contact__item">
          <svg viewBox="0 0 24 24" fill="none" stroke="#fff" stroke-width="2"><circle cx="12" cy="12" r="9"/><path d="M3 12h18M12 3a14 14 0 0 1 0 18M12 3a14 14 0 0 0 0 18"/></svg>
          www.resinworkshub.ca
        </li>
        <li class="contact__item">
          <svg viewBox="0 0 24 24" fill="none" stroke="#fff" stroke-width="2"><rect x="3" y="5" width="18" height="14" rx="1"/><path d="M3 6l9 7 9-7"/></svg>
          ted@resinworkshub.ca
        </li>
      </ul>
    </div>
    <p class="address">7-4812 Fernhollow Road, Abbotsford, BC, V3K 8R2.</p>
  </section>
</main>
</body>
</html>
```